BOLD & MINIMALIST DESIGN NEEDED

We want a very bold but minimalistic business card design that is impactful and utilizes both sides of the business card. Our current logo is included for your use.

We want bold fonts and good use of negative space. We don't want the logo to overpower the design.

Target Market(s)

Professionals who are building new commercial buildings.

Industry/Entity Type

Construction

Contact Information for Business Card

Name, Title, email, office phone, cell phone, website

Font styles to use
Serif
Sans Serif

Requirements
Must have
• Bold design!

```html
<!DOCTYPE html>
<html lang="en">
<head>
<meta charset="utf-8">
<title>Summitline Design + Build — Business Card</title>
<link rel="stylesheet" href="https://fonts.googleapis.com/css2?family=Arimo:wght@400;700&display=swap">
<style>
  :root {
    --canvas-bg: #e4e4e4;
    --green-light: #b7dd85;
    --green-mid: #9ccf55;
    --green-deep: #86c22a;
    --ink: #111111;
    --paper: #ffffff;
  }
  * { box-sizing: border-box; margin: 0; padding: 0; }
  html, body {
    width: 1200px;
    height: 1200px;
    overflow: hidden;
    background: var(--canvas-bg);
    font-family: "Arimo", Arial, sans-serif;
    color: var(--ink);
  }
  .canvas {
    position: relative;
    width: 1200px;
    height: 1200px;
  }
  .card {
    position: absolute;
    width: 690px;
    height: 393px;
  }
  .card--front {
    left: 267px;
    top: 159px;
    background: radial-gradient(ellipse 55% 60% at 50% 50%, var(--green-light) 0%, var(--green-mid) 55%, var(--green-deep) 100%);
  }
  .card--back {
    left: 262px;
    top: 653px;
    background: var(--paper);
  }
  .identity {
    position: absolute;
    right: 367px;
    top: 172px;
    text-align: right;
  }
  .identity__name {
    font-weight: 700;
    font-size: 25px;
    letter-spacing: 0.3px;
    line-height: 1;
  }
  .identity__title {
    margin-top: 10px;
    font-size: 15px;
    line-height: 1;
  }
  .divider {
    position: absolute;
    left: 340px;
    top: 156px;
    width: 1px;
    height: 83px;
    background: var(--ink);
  }
  .contacts {
    position: absolute;
    left: 354px;
    top: 158px;
    list-style: none;
  }
  .contacts__item {
    display: flex;
    align-items: center;
    height: 20.5px;
    font-size: 16px;
  }
  .contacts__icon {
    width: 14px;
    height: 14px;
    margin-right: 10px;
    flex: none;
  }
  .brand {
    position: absolute;
    left: 0;
    right: 0;
    top: 170px;
    display: flex;
    justify-content: center;
    align-items: center;
    gap: 14px;
  }
  .brand__mark {
    width: 34px;
    height: 34px;
    background: var(--green-deep);
  }
  .brand__name {
    font-weight: 700;
    font-size: 34px;
    letter-spacing: 1px;
    color: var(--ink);
    text-transform: uppercase;
  }
</style>
</head>
<body>
<main class="canvas">
  <section class="card card--front" aria-label="Card front">
    <div class="identity">
      <p class="identity__name">DANIEL REYES</p>
      <p class="identity__title">President</p>
    </div>
    <div class="divider"></div>
    <ul class="contacts">
      <li class="contacts__item">
        <svg class="contacts__icon" viewBox="0 0 16 16" aria-hidden="true"><path fill="#111" d="M3.2 1.2l2.3 2.6-1.2 1.8c.9 2 2.2 3.4 4.2 4.3l1.8-1.2 2.6 2.3-1.4 2.4C6.6 13 2.8 9.2 1 4.3z"/></svg>
        555-210-4870
      </li>
      <li class="contacts__item">
        <svg class="contacts__icon" viewBox="0 0 16 16" aria-hidden="true"><rect x="4" y="1" width="8" height="14" rx="1.2" fill="none" stroke="#111" stroke-width="1.6"/><rect x="7" y="12" width="2" height="1.2" fill="#111"/></svg>
        555-318-6925
      </li>
      <li class="contacts__item">
        <svg class="contacts__icon" viewBox="0 0 16 16" aria-hidden="true"><rect x="1" y="4" width="14" height="9" fill="#111"/><path d="M1.5 4.5L8 9.5l6.5-5" fill="none" stroke="#9ccf55" stroke-width="1.2"/></svg>
        info@summitlinebuild.com
      </li>
      <li class="contacts__item">
        <svg class="contacts__icon" viewBox="0 0 16 16" aria-hidden="true"><circle cx="8" cy="8" r="6.5" fill="#111"/><path d="M5 4.5c1.5.5 2 1.5 1.5 2.5-.6 1 .5 2 1.5 2.2.8.2.6 1.8 0 2.8M10 4c-.5 1 .5 1.6 1.8 1.8" fill="none" stroke="#9ccf55" stroke-width="1"/></svg>
        www.summitlinebuild.com
      </li>
    </ul>
  </section>

  <section class="card card--back" aria-label="Card back">
    <div class="brand">
      <span class="brand__mark" aria-hidden="true"></span>
      <span class="brand__name">Summitline Design + Build</span>
    </div>
  </section>
</main>
</body>
</html>
```